Fern Lattice Table & Chair Rentals

We need a business card for a table and chair rental company. We rent tables and chairs for weddings, funerals, business events and parties. We want something that looks clean and elegant while not being too busy. We would like colors in the green and blue hues and avoiding anything orange. We want to make sure the font is large enough to be seen easily.

Target Market(s)

Wedding & Event Rentals

Industry/Entity Type

Events

Contact Information for Business Card

Fern Lattice, sales@fernlatticerentals.com, fernlatticerentals.com, 360-555-0182

Requirements
Must have
• Easy to read font
Should not have
• Orange anywhere in the design

```html
<!DOCTYPE html>
<html lang="en">
<head>
<meta charset="utf-8">
<title>Fern Lattice Table &amp; Chair Rentals – Business Card</title>
<link rel="stylesheet" href="https://fonts.googleapis.com/css2?family=Open+Sans:ital,wght@0,400;0,600;1,400&family=Roboto:wght@400;500&display=swap">
<style>
  :root {
    --page: #e6e9e8;
    --card-black: #0b0d0e;
    --band-green: #2e9e85;
    --rule-blue: #2f7fb5;
    --ink-white: #ffffff;
    --ink-dark: #0a1e1a;
  }
  * { box-sizing: border-box; margin: 0; padding: 0; }
  html, body {
    width: 1200px; height: 892px; overflow: hidden;
    background: var(--page);
  }
  .canvas {
    width: 1200px; height: 892px;
    display: flex; flex-direction: column; align-items: center; justify-content: center;
    gap: 44px;
  }
  .card {
    position: relative;
    width: 660px; height: 377px;
    border-radius: 22px;
    background: var(--card-black);
    overflow: hidden;
    box-shadow: 0 10px 28px rgba(0,0,0,0.25);
  }
  .band {
    position: absolute; left: 0; right: 0; bottom: 0;
    background: var(--band-green);
  }
  .band-rule {
    position: absolute; left: 0; right: 0; height: 4px;
    background: var(--rule-blue);
  }

  /* Front */
  .front .brand {
    position: absolute; left: 150px; top: 48px;
    font-family: "Open Sans", sans-serif; font-weight: 600;
    font-size: 74px; line-height: 1; letter-spacing: -1px;
    color: var(--ink-white);
  }
  .front .tagline {
    position: absolute; left: 120px; top: 150px;
    font-family: "Open Sans", sans-serif; font-weight: 400;
    font-size: 40px; color: var(--ink-white); letter-spacing: 0.5px;
  }
  .front .band-rule { top: 232px; }
  .front .band { height: 130px; border-radius: 18px 0 0 0; left: 24px; }
  .hours {
    position: absolute; left: 24px; right: 0; bottom: 0; height: 130px;
    display: flex; align-items: center; justify-content: space-between;
    padding: 0 26px;
    font-family: "Open Sans", sans-serif; font-style: italic;
    font-size: 18px; color: var(--ink-dark); white-space: nowrap;
  }

  /* Back */
  .back .brand {
    position: absolute; left: 70px; top: 40px;
    font-family: "Open Sans", sans-serif; font-weight: 600;
    font-size: 58px; line-height: 1; color: var(--ink-white);
  }
  .back .tagline {
    position: absolute; left: 72px; top: 108px;
    font-family: "Open Sans", sans-serif; font-size: 25px; color: var(--ink-white);
  }
  .back .company {
    position: absolute; left: 72px; top: 158px;
    font-family: "Roboto", sans-serif; font-size: 36px; color: var(--ink-white);
  }
  .back .phone {
    position: absolute; left: 270px; top: 210px;
    font-family: "Roboto", sans-serif; font-weight: 500; font-size: 40px; color: var(--ink-white);
    letter-spacing: 1px;
  }
  .back .band-rule { top: 286px; }
  .back .band { height: 84px; }
  .contact {
    position: absolute; left: 0; right: 0; bottom: 0; height: 84px;
    display: flex; align-items: center; justify-content: space-between;
    padding: 0 34px;
    font-family: "Open Sans", sans-serif; font-size: 20px; color: var(--ink-dark);
    white-space: nowrap;
  }
</style>
</head>
<body>
<main class="canvas">

  <section class="card front" aria-label="Card front">
    <div class="brand">Fern Lattice</div>
    <div class="tagline">Table and Chair Rentals</div>
    <div class="band-rule"></div>
    <div class="band"></div>
    <div class="hours">
      <span>Mon-Fri: 8am to 6pm</span>
      <span>Saturday: 8am to 4pm</span>
      <span>Sunday: 9am to 1pm</span>
    </div>
  </section>

  <section class="card back" aria-label="Card back">
    <div class="brand">Fern Lattice</div>
    <div class="tagline">Table and Chair Rentals</div>
    <div class="company">Fernlattice Event Rentals, LLC</div>
    <div class="phone">360-555-0182</div>
    <div class="band-rule"></div>
    <div class="band"></div>
    <div class="contact">
      <span>www.fernlatticerentals.com</span>
      <span>sales@fernlatticerentals.com</span>
    </div>
  </section>

</main>
</body>
</html>
```